20 year old business card needs re-design

We need to redesign our corporate business card look. We need something that appears more modern, eye catchy but professional.

Target Market(s)

manufacturing industry

Industry/Entity Type

Manufacturer

Contact Information for Business Card

One side can have the logo. Other side can have contact information.

Font styles to use
Serif

Colors
3277b5
33b8a4
ffffff

Requirements
Must have
• Eye catchy - need to standout from the crowd. company logo cannot change. Full name, job title, phone number and email address.
Should not have
• Fax, business address is not necessary.

```html
<!DOCTYPE html>
<html lang="en">
<head>
<meta charset="utf-8">
<title>Norvex International – Business Card</title>
<link rel="stylesheet" href="https://fonts.googleapis.com/css2?family=Arimo:wght@400;700&display=swap">
<style>
  :root {
    --page-bg: #2a2a2a;
    --card-white: #ffffff;
    --brand-blue: #1f4f9f;
    --ink-dark: #1e1c1d;
    --ink-text: #2b2b2b;
    --ink-light: #ffffff;
    --icon-line: #d9d9d9;
  }
  * { box-sizing: border-box; margin: 0; padding: 0; }
  html, body {
    width: 1200px; height: 997px; overflow: hidden;
    background: var(--page-bg);
    font-family: "Arimo", Arial, sans-serif;
  }
  .canvas {
    width: 1200px; height: 997px;
    display: flex; flex-direction: column;
    align-items: center; justify-content: center; gap: 60px;
  }
  .card {
    position: relative;
    width: 700px; height: 400px;
    background: var(--card-white);
    overflow: hidden;
    box-shadow: 0 12px 30px rgba(0,0,0,0.45);
  }
  .brand {
    display: flex; align-items: center; gap: 16px;
    color: var(--brand-blue);
    font-weight: 700;
    letter-spacing: 1px;
  }
  .brand-mark {
    width: 30px; height: 30px;
    background: var(--brand-blue);
  }
  .card-front .brand {
    position: absolute; inset: 0;
    justify-content: center;
    font-size: 50px;
  }
  .card-back .brand {
    position: absolute; left: 0; right: 0; top: 70px;
    justify-content: center;
    font-size: 40px;
  }
  .card-back .brand-mark { width: 24px; height: 24px; }

  .info-band {
    position: absolute; left: 0; right: 0; top: 190px; height: 140px;
    display: flex;
  }
  .person {
    position: relative;
    width: 330px; height: 100%;
    background: var(--brand-blue);
    color: var(--ink-light);
    padding: 62px 0 0 50px;
  }
  .person-notch {
    position: absolute; left: 150px; top: 0;
    width: 0; height: 0;
    border-left: 16px solid transparent;
    border-right: 16px solid transparent;
    border-top: 14px solid var(--ink-dark);
  }
  .person-name { font-size: 22px; font-weight: 700; letter-spacing: 0.5px; }
  .person-title { font-size: 17px; font-weight: 700; margin: 4px 0 0 38px; }
  .contacts {
    position: relative;
    flex: 1; height: 100%;
    background: var(--ink-dark);
    color: var(--ink-light);
    padding: 18px 0 0 60px;
    list-style: none;
  }
  .contacts-pointer {
    position: absolute; left: 0; top: 52px;
    width: 0; height: 0;
    border-top: 16px solid transparent;
    border-bottom: 16px solid transparent;
    border-left: 16px solid var(--card-white);
  }
  .contact-item {
    display: flex; align-items: center; gap: 14px;
    font-size: 15px; height: 28px;
  }
  .contact-icon {
    width: 20px; height: 20px; flex: none;
  }
  .address {
    position: absolute; left: 0; right: 0; bottom: 0; height: 70px;
    display: flex; align-items: center;
    padding-left: 40px;
    font-size: 15px; font-weight: 700;
    color: var(--ink-text);
  }
</style>
</head>
<body>
<main class="canvas">
  <section class="card card-front" aria-label="Card front">
    <div class="brand"><span class="brand-mark"></span>Norvex International</div>
  </section>

  <section class="card card-back" aria-label="Card back">
    <div class="brand"><span class="brand-mark"></span>Norvex International</div>
    <div class="info-band">
      <div class="person">
        <span class="person-notch"></span>
        <div class="person-name">DANIEL HARLOW</div>
        <div class="person-title">Director</div>
      </div>
      <ul class="contacts">
        <span class="contacts-pointer"></span>
        <li class="contact-item">
          <svg class="contact-icon" viewBox="0 0 20 20"><circle cx="10" cy="10" r="9" fill="none" stroke="var(--icon-line)" stroke-width="1.4"/><path d="M6 8c0-1.5 8-1.5 8 0v1h-2V8H8v1H6z M7 10h6l1 4H6z" fill="var(--icon-line)"/></svg>
          (555) 210-4832
        </li>
        <li class="contact-item">
          <svg class="contact-icon" viewBox="0 0 20 20"><circle cx="10" cy="10" r="9" fill="none" stroke="var(--icon-line)" stroke-width="1.4"/><rect x="6" y="8" width="8" height="6" fill="var(--icon-line)"/><rect x="7.5" y="5.5" width="5" height="3" fill="none" stroke="var(--icon-line)" stroke-width="1"/></svg>
          (555) 210-4833
        </li>
        <li class="contact-item">
          <svg class="contact-icon" viewBox="0 0 20 20"><circle cx="10" cy="10" r="9" fill="none" stroke="var(--icon-line)" stroke-width="1.4"/><rect x="5.5" y="7" width="9" height="6.5" fill="none" stroke="var(--icon-line)" stroke-width="1.2"/><path d="M5.5 7l4.5 3.5L14.5 7" fill="none" stroke="var(--icon-line)" stroke-width="1.2"/></svg>
          dharlow@norvexintl.com
        </li>
      </ul>
    </div>
    <p class="address">418 W. Alder Street, Suite 920, P.O. Box 31055, Brookhaven, Ohio 44120</p>
  </section>
</main>
</body>
</html>
```